Catalogue Design Project

We need a catalog design for a new private university called Redwell Institute Bayshore (see website www.rwi-bs.org). The catalog should be about 30 pages maximum and will include items such as General Information, Academic schedule, department descriptions, program descriptions, course descriptions, school policies, student services, admissions, San diego Lifestyle, etc.
I will provide the text but I need a professional design with regard to page layouts. I have provided some examples.
Ok, i posted the catalog content, just missing course descriptions.
Target Market(s)
Young Professionals, Foreign Students
Industry/Entity Type
University
Look and feel
Each slider illustrates characteristics of the customer's brand and the style your logo design should communicate.

```html
<!DOCTYPE html>
<html lang="en">
<head>
<meta charset="utf-8">
<title>Academic Programs – Marketing Certificate</title>
<link rel="stylesheet" href="https://fonts.googleapis.com/css2?family=Carlito:wght@400;700&display=swap">
<style>
  :root {
    --ink: #1a1a1a;
    --navy: #2e5f93;
    --navy-deep: #1f4a78;
    --rule: #a9bdd3;
    --muted: #8a8a8a;
    --motif-grey: #b3b3b3;
    --paper: #ffffff;
    --book-light: #f3ede2;
    --book-mid: #d9cdb6;
  }
  html, body {
    margin: 0;
    padding: 0;
    overflow: hidden;
    background: var(--paper);
  }
  .page {
    position: relative;
    width: 927px;
    height: 1200px;
    overflow: hidden;
    background: var(--paper);
    font-family: "Carlito", "Calibri", sans-serif;
    color: var(--ink);
  }
  .header-visual {
    position: absolute;
    left: 440px;
    top: 0;
    width: 487px;
    height: 150px;
    background:
      linear-gradient(to right, var(--paper) 0%, rgba(255,255,255,0) 45%),
      linear-gradient(to bottom, rgba(255,255,255,0) 55%, var(--paper) 100%),
      linear-gradient(160deg, var(--book-mid) 0%, var(--book-light) 55%, #ece4d4 100%);
  }
  .header-motif {
    position: absolute;
    left: 60px;
    top: 57px;
    width: 152px;
    height: 34px;
    border-radius: 6px;
    background: linear-gradient(to right, var(--motif-grey) 0%, #9fb2c8 100%);
  }
  .section-title {
    position: absolute;
    left: 306px;
    top: 95px;
    margin: 0;
    font-weight: 400;
    font-size: 30px;
    line-height: 36px;
    color: var(--ink);
  }
  .section-bar {
    position: absolute;
    left: 306px;
    top: 133px;
    width: 316px;
    height: 16px;
    background: var(--navy);
  }
  .header-rule {
    position: absolute;
    left: 0;
    top: 151px;
    width: 927px;
    height: 2px;
    background: var(--rule);
  }
  .category-tab {
    position: absolute;
    left: 0;
    top: 178px;
    width: 427px;
    height: 42px;
    background: linear-gradient(to bottom, var(--navy) 0%, var(--navy-deep) 100%);
    border-radius: 0 12px 12px 0;
    box-shadow: 2px 2px 3px rgba(0,0,0,0.25);
    color: #fff;
    font-size: 30px;
    line-height: 42px;
    padding-left: 62px;
    box-sizing: border-box;
  }
  .content {
    position: absolute;
    left: 80px;
    top: 246px;
    width: 803px;
    font-size: 19.6px;
  }
  .program-title {
    margin: 0 0 3px;
    text-align: center;
    font-size: 23px;
    line-height: 32px;
    font-weight: 700;
  }
  .program-intro p {
    margin: 0;
    line-height: 37.5px;
    text-align: justify;
  }
  .program-facts {
    margin: 0;
    line-height: 27px;
  }
  .program-facts strong { font-weight: 700; }
  .course-list {
    margin: 25px 0 0;
    padding: 0;
    list-style: none;
    line-height: 27px;
  }
  .list-heading {
    text-decoration: underline;
  }
  .learning-outcome {
    margin: 25px 0 0;
    line-height: 28px;
  }
  .footer-rule {
    position: absolute;
    left: 0;
    top: 1156px;
    width: 927px;
    height: 1px;
    background: var(--rule);
  }
  .footer-mark {
    position: absolute;
    right: 36px;
    top: 1171px;
    font-size: 13px;
    color: var(--muted);
    letter-spacing: 0.3px;
  }
</style>
</head>
<body>
<div class="page">
  <div class="header-visual" role="img" aria-label="Photograph of an open antique book, fading into the page"></div>
  <div class="header-motif" role="img" aria-label="Decorative cluster of grey and blue dots"></div>

  <h1 class="section-title">ACADEMIC PROGRAMS</h1>
  <div class="section-bar"></div>
  <div class="header-rule"></div>

  <div class="category-tab">CERTIFICATE PROGRAMS</div>

  <main class="content">
    <h2 class="program-title">Marketing Certificate</h2>
    <div class="program-intro">
      <p>The Marketing Certificate is designed for students who are interested in studying basic as well as advanced concepts related to Marketing and want to put them to use in real-world opportunities. Students will have the opportunity to construct actual marketing plans to add to their portfolios as well as utilize for achievement of personal objectives.</p>
      <p>Specifically, students will learn to build and sustain successful, integrated interactive marketing programs that can be used for both a current company project or for one's own business. Strong class focus will be on use of digital marketing methods to generate Internet traffic, search engine optimization, search engine marketing, as well as mobile and email marketing techniques.</p>
    </div>
    <div class="program-facts">
      <div><strong>Hours:</strong> 6 hours per week</div>
      <div><strong>Length:</strong> 8 weeks per course</div>
    </div>

    <ul class="course-list">
      <li class="list-heading">Required Courses:</li>
      <li>BUS 601 Statistics</li>
      <li>MKT 600 Marketing Principles</li>
      <li>MKT 601 Marketing Research</li>
    </ul>

    <ul class="course-list">
      <li class="list-heading">Elective Courses: (Choose 2)</li>
      <li>MKT 602 Internet Advertising Solutions</li>
      <li>MKT 603 Consumer Behavior</li>
      <li>MKT 604 Global Marketing</li>
      <li>MKT 605 E-commerce</li>
      <li>MKT 607 Marketing Internship</li>
      <li>BUS 600 Starting Your Own Business</li>
    </ul>

    <div class="learning-outcome">
      <div class="list-heading">Learning Outcome:</div>
      <div>Strong comprehension of offline and online marketing practices, knowledge of marketing plan production and implementation of tools to design and sell a product successfully.</div>
    </div>
  </main>

  <div class="footer-rule"></div>
  <div class="footer-mark">11::: REDWELL INSTITUTE</div>
</div>
</body>
</html>
```